New Business Card for Software Company

We are looking at rebranding a 10 year old company that specializes in PDF and DWF solutions for Architects and Engineers. We will attach the new company logo that we are going with so you can work with that and complimentary colors.
The sample information we would like on the business card is:
Gerald Pinfold
Vice President
4738 W. Harrowgate Lane. STE 305
PMB#417
Mesa, AZ 85374
866-392-5074 US Toll Free
123-456-3190 Cell
gpinfold@plavorix.com
The old tag line that we had on the business cars was.
Providing Industrial Strength PDF and DWF Solutions to the Global CAD Marketplace.
If you have an idea for a better tag line we are open to that also.
Updates
We would like to thank all of the Designers for their wonderful work. We apologize that we will not have the time to provide feedback to everyone. There is just so many innovative and professional designs that you have all created making our decision even harder.
Target Market(s)
Architects and Engineers
Industry/Entity Type
Business
Look and feel

```html
<!DOCTYPE html>
<html lang="en">
<head>
<meta charset="utf-8">
<title>Plavorix Business Card</title>
<link rel="stylesheet" href="https://fonts.googleapis.com/css2?family=Source+Sans+3:wght@400;600;700;800&display=swap">
<style>
  :root {
    --bg: #e9e6e1;
    --card: #ffffff;
    --orange: #ee5a24;
    --orange-light: #f7941d;
    --red: #c4161c;
    --grey: #6d6e71;
    --text: #4d4d4f;
    --white: #ffffff;
  }
  * { margin: 0; padding: 0; box-sizing: border-box; }
  html, body { width: 1200px; height: 720px; overflow: hidden; }
  body {
    background: var(--bg);
    font-family: "Source Sans 3", sans-serif;
    position: relative;
  }
  .card {
    position: absolute;
    top: 206px;
    width: 540px;
    height: 308px;
    background: var(--card);
    box-shadow: 0 4px 14px rgba(0,0,0,0.12);
    overflow: hidden;
  }
  .card--front { left: 40px; }
  .card--back { left: 620px; }

  .swoosh { position: absolute; inset: 0; width: 100%; height: 100%; }

  .brand {
    position: absolute;
    left: 30px;
    top: 40px;
    display: flex;
    align-items: center;
    gap: 12px;
  }
  .brand__dot {
    width: 42px; height: 42px;
    border-radius: 50%;
    background: var(--orange);
  }
  .brand__name {
    font-weight: 800;
    font-size: 46px;
    letter-spacing: -1px;
    color: var(--orange);
    line-height: 1;
  }

  .person {
    position: absolute;
    left: 32px;
    top: 138px;
    color: var(--text);
  }
  .person__name {
    font-weight: 700;
    font-size: 17px;
    color: var(--orange);
    line-height: 1.1;
  }
  .person__title {
    font-size: 12px;
    color: var(--grey);
    margin-bottom: 14px;
  }
  .person__address {
    font-size: 13px;
    line-height: 1.35;
    font-weight: 600;
    color: var(--text);
  }

  .contact {
    position: absolute;
    right: 24px;
    top: 112px;
    list-style: none;
    color: var(--white);
    font-size: 13px;
    font-weight: 600;
    text-align: right;
  }
  .contact li {
    display: flex;
    justify-content: flex-end;
    align-items: center;
    gap: 7px;
    margin-bottom: 10px;
  }
  .contact li:last-child { margin-top: 16px; }
  .contact svg { width: 12px; height: 12px; fill: var(--white); flex: none; }

  .back__brand {
    position: absolute;
    left: 0; right: 0;
    top: 92px;
    text-align: center;
    font-weight: 800;
    font-size: 84px;
    letter-spacing: -2px;
    color: var(--orange);
    line-height: 1;
  }
  .back__tagline {
    position: absolute;
    left: 0; right: 0;
    top: 205px;
    text-align: center;
    font-size: 17px;
    line-height: 1.3;
    color: var(--grey);
  }
</style>
</head>
<body>

  <section class="card card--front" aria-label="Business card front">
    <svg class="swoosh" viewBox="0 0 540 308" preserveAspectRatio="none" aria-hidden="true">
      <defs>
        <linearGradient id="band-fill" x1="0" y1="1" x2="1" y2="0">
          <stop offset="0" stop-color="#f7941d"/>
          <stop offset="0.45" stop-color="#ee5a24"/>
          <stop offset="1" stop-color="#c4161c"/>
        </linearGradient>
      </defs>
      <path d="M0,262 C150,300 250,200 330,120 C380,70 450,40 540,30 L540,308 L0,308 Z" fill="url(#band-fill)"/>
      <path d="M0,250 C150,288 250,188 330,108 C380,58 450,28 540,18" fill="none" stroke="#6d6e71" stroke-width="7"/>
      <path d="M0,280 C150,312 300,262 540,236 L540,250 C320,272 170,320 0,300 Z" fill="#6d6e71"/>
    </svg>

    <div class="brand">
      <span class="brand__dot"></span>
      <span class="brand__name">Plavorix</span>
    </div>

    <div class="person">
      <p class="person__name">Gerald Pinfold</p>
      <p class="person__title">Vice President</p>
      <p class="person__address">4738 W. Harrowgate Lane. STE 305<br>PMB#417, Mesa, AZ 85374</p>
    </div>

    <ul class="contact">
      <li>
        <svg viewBox="0 0 24 24" aria-hidden="true"><path d="M6.6 10.8c1.4 2.8 3.8 5.1 6.6 6.6l2.2-2.2c.3-.3.7-.4 1-.2 1.1.4 2.3.6 3.6.6.6 0 1 .4 1 1V20c0 .6-.4 1-1 1C10.6 21 3 13.4 3 4c0-.6.4-1 1-1h3.5c.6 0 1 .4 1 1 0 1.3.2 2.5.6 3.6.1.3 0 .7-.2 1z"/></svg>
        866-392-5074 US(TF)
      </li>
      <li>
        <svg viewBox="0 0 24 24" aria-hidden="true"><path d="M7 1h10c1.1 0 2 .9 2 2v18c0 1.1-.9 2-2 2H7c-1.1 0-2-.9-2-2V3c0-1.1.9-2 2-2zm0 4v12h10V5H7zm5 14.5a1.2 1.2 0 1 0 0 2.4 1.2 1.2 0 0 0 0-2.4z"/></svg>
        123-456-3190
      </li>
      <li>
        <svg viewBox="0 0 24 24" aria-hidden="true"><path d="M2 5h20v14H2zm2 2v.5l8 5 8-5V7zm0 2.8V17h16V9.8l-8 5z"/></svg>
        gpinfold@plavorix.com
      </li>
    </ul>
  </section>

  <section class="card card--back" aria-label="Business card back">
    <p class="back__brand">Plavorix</p>
    <p class="back__tagline">Providing Industrial Strength PDF and<br>DWF Solutions to the Global CAD Marketplace</p>
  </section>

</body>
</html>
```